Small Business Broker Business Card Design

A business card design for a small business brokerage, which is a financial service, not unlike real estate brokerage, but for small businesses such as laundromats, pizza shops, restaurants, cleaners etc. The designs should all be simple, more conservative in nature, using the colors and font of the logo. Again, think real estate Brokerage as a business context
Contact Information for Business Card
Name: Glen R. Harlow. Title: Small Business Advisor. Email: g.harlow@bayfieldcapitalworks.example. Mobile: (555) 274-3918. Office: (555) 806-2147. www.bayfieldcapitalworks.example

```html
<!DOCTYPE html>
<html lang="en">
<head>
<meta charset="utf-8">
<title>Bayfield Capital Works – Business Card</title>
<link rel="stylesheet" href="https://fonts.googleapis.com/css2?family=Open+Sans:wght@400;600;700&display=swap">
<style>
  :root {
    --stage: #222222;
    --card: #1b1b1b;
    --card-edge: #2a2a2a;
    --green: #8cc63f;
    --blue: #1f4e8c;
    --white: #f4f4f4;
    --rule: #bdbdbd;
    --pattern-dark: #141414;
    --pattern-light: #8a8a8a;
  }
  * { box-sizing: border-box; margin: 0; padding: 0; }
  html, body {
    width: 1200px; height: 780px; overflow: hidden;
    background: var(--stage);
    font-family: "Open Sans", Arial, sans-serif;
  }
  .canvas {
    position: relative; width: 1200px; height: 780px;
    display: flex; align-items: center; justify-content: center; gap: 40px;
  }
  .card {
    position: relative; width: 550px; height: 314px;
    background: var(--card);
    border: 1px solid var(--card-edge);
    box-shadow: 0 18px 40px rgba(0,0,0,.55);
    overflow: hidden;
  }

  /* Front */
  .brand {
    position: absolute; left: 40px; top: 54px;
    display: flex; align-items: center; gap: 10px;
  }
  .brand-square { width: 24px; height: 24px; background: var(--blue); flex: none; }
  .brand-name {
    font-size: 13px; font-weight: 600; color: var(--blue);
    letter-spacing: .04em; text-transform: uppercase; line-height: 1.3;
    width: 130px;
  }
  .divider { position: absolute; left: 0; top: 0; width: 550px; height: 314px; pointer-events: none; }
  .identity { position: absolute; left: 256px; top: 58px; }
  .person-name { font-size: 30px; font-weight: 700; line-height: 1.1; white-space: nowrap; }
  .person-name .first { color: var(--green); }
  .person-name .last { color: var(--blue); }
  .person-title { margin-top: 4px; font-size: 15px; font-weight: 600; color: var(--white); }
  .contacts { list-style: none; margin-top: 20px; }
  .contacts li {
    display: flex; align-items: center; gap: 9px;
    font-size: 12px; color: var(--white); margin-bottom: 8px; white-space: nowrap;
  }
  .contacts svg { width: 14px; height: 14px; flex: none; }
  .address {
    position: absolute; left: 40px; bottom: 32px;
    font-size: 14px; color: var(--white); letter-spacing: .01em;
  }

  /* Back */
  .pattern-field {
    position: absolute; inset: 0;
    background: linear-gradient(100deg, var(--pattern-dark) 0%, #1d1d1d 55%, #3a3a3a 80%, var(--pattern-light) 100%);
  }
  .back-brand {
    position: absolute; left: 50%; top: 58%; transform: translate(-50%, -50%);
    display: flex; align-items: center; gap: 8px;
  }
  .back-brand .brand-square { width: 14px; height: 14px; }
  .back-brand .brand-name { width: auto; font-size: 9px; white-space: nowrap; }
</style>
</head>
<body>
<main class="canvas">

  <section class="card card-front" aria-label="Business card front">
    <div class="brand">
      <span class="brand-square"></span>
      <span class="brand-name">Bayfield Capital Works Inc</span>
    </div>

    <svg class="divider" viewBox="0 0 550 314" aria-hidden="true">
      <line x1="238" y1="44" x2="190" y2="244" stroke="var(--rule)" stroke-width="0.8"/>
    </svg>

    <div class="identity">
      <h1 class="person-name"><span class="first">Glen R.</span> <span class="last">Harlow</span></h1>
      <p class="person-title">Small Business Advisor</p>
      <ul class="contacts">
        <li>
          <svg viewBox="0 0 16 16" aria-hidden="true"><path d="M4 1.5l2.2 3-1.3 1.6c.9 2 2.4 3.5 4.4 4.4l1.6-1.3 3 2.2-1.2 2.6C7.5 14 2 8.5 1.4 2.7z" fill="var(--green)"/></svg>
          (555) 274-3918
        </li>
        <li>
          <svg viewBox="0 0 16 16" aria-hidden="true"><rect x="1" y="3" width="14" height="10" rx="1" fill="var(--green)"/><path d="M1.5 3.8L8 9l6.5-5.2" fill="none" stroke="var(--card)" stroke-width="1.3"/></svg>
          g.harlow@bayfieldcapitalworks.example
        </li>
        <li>
          <svg viewBox="0 0 16 16" aria-hidden="true"><circle cx="8" cy="8" r="7" fill="var(--green)"/><path d="M1 8h14M8 1c-2.6 2.5-2.6 11.5 0 14M8 1c2.6 2.5 2.6 11.5 0 14" fill="none" stroke="var(--card)" stroke-width="1"/></svg>
          www.bayfieldcapitalworks.example
        </li>
      </ul>
    </div>

    <p class="address">1840 Harlan Ave. Suite 300 Bayfield, TX 75010</p>
  </section>

  <section class="card card-back" aria-label="Business card back">
    <div class="pattern-field" role="img" aria-label="Repeating chevron pattern in black and grey tones"></div>
    <div class="back-brand">
      <span class="brand-square"></span>
      <span class="brand-name">Bayfield Capital Works Inc</span>
    </div>
  </section>

</main>
</body>
</html>
```